Awesome photographers card for an awesome new business

Double sided business card Black background and silver logo in middle on one side. Details on otherside. please keep it simple

Industry/Entity Type

Photographer

Contact Information for Business Card

Gerald Fenwick
0452817360
GeraldFenwickPhotography47@mailbox.test
www.GeraldFenwickPhotography.test.au
Instagram _Gerald_fenwick

Requirements
Must have
• My logo in Silver
• please use instagram logo instead of "Instagram"

```html
<!DOCTYPE html>
<html lang="en">
<head>
<meta charset="utf-8">
<title>Gerald Fenwick Photography – Business Card</title>
<link href="https://fonts.googleapis.com/css2?family=Roboto:wght@400;500&family=Roboto+Condensed:wght@700&display=swap" rel="stylesheet">
<style>
  :root {
    --backdrop: #262626;
    --card-light: #f4f4f4;
    --card-dark: #1b1c1d;
    --ink: #555555;
    --ink-name: #5a5a5a;
    --silver: #c9c9c9;
    --silver-text: #e6e6e6;
    --logo-grey: #777777;
  }
  * { margin: 0; padding: 0; box-sizing: border-box; }
  html, body { width: 1200px; height: 960px; overflow: hidden; }
  body {
    background: var(--backdrop);
    position: relative;
    font-family: "Roboto", Arial, sans-serif;
  }
  .card {
    position: absolute;
    width: 600px;
    height: 342px;
  }
  .card--front { left: 314px; top: 113px; background: var(--card-light); }
  .card--back { left: 312px; top: 473px; background: var(--card-dark); }

  .brand-mark {
    position: absolute;
    left: 50%;
    transform: translateX(-50%);
    border-radius: 50%;
    display: flex;
    align-items: center;
    justify-content: center;
    text-align: center;
  }
  .card--front .brand-mark {
    top: 52px;
    width: 144px; height: 144px;
    border: 3px solid var(--logo-grey);
  }
  .card--back .brand-mark {
    top: 64px;
    width: 180px; height: 180px;
    border: 3px solid var(--silver);
  }
  .brand-name {
    font-family: "Roboto", Arial, sans-serif;
    font-weight: 500;
    letter-spacing: 1px;
    line-height: 1.3;
  }
  .card--front .brand-name { font-size: 15px; color: var(--logo-grey); }
  .card--back .brand-name { font-size: 18px; color: var(--silver); }

  .holder-name {
    position: absolute;
    top: 230px; left: 0; right: 0;
    text-align: center;
    font-family: "Roboto Condensed", "Arial Narrow", sans-serif;
    font-weight: 700;
    font-size: 20px;
    color: var(--ink-name);
  }
  .contact-lines {
    position: absolute;
    top: 264px; left: 0; right: 0;
    text-align: center;
    font-size: 14.5px;
    color: var(--ink);
    line-height: 19px;
  }
  .contact-row { display: flex; justify-content: center; gap: 6px; }
  .contact-item { display: inline-flex; align-items: center; gap: 4px; white-space: nowrap; }
  .contact-icon { width: 13px; height: 13px; flex: none; }
  .contact-icon--fill { fill: var(--ink); }
  .contact-icon--line { fill: none; stroke: var(--ink); stroke-width: 2.2; }
  .social-square {
    display: inline-block; width: 12px; height: 12px; flex: none;
    background: var(--ink); border-radius: 2px;
  }
  .back-web {
    position: absolute;
    top: 290px; left: 0; right: 0;
    text-align: center;
    font-size: 15px;
    letter-spacing: 2px;
    color: var(--silver-text);
  }
</style>
</head>
<body>
  <section class="card card--front" aria-label="Business card, details side">
    <div class="brand-mark"><span class="brand-name">Gerald<br>Fenwick</span></div>
    <h1 class="holder-name">GERALD FENWICK</h1>
    <div class="contact-lines">
      <div class="contact-row">
        <span class="contact-item">
          <svg class="contact-icon contact-icon--fill" viewBox="0 0 24 24" aria-hidden="true"><path d="M6.6 10.8a15.1 15.1 0 0 0 6.6 6.6l2.2-2.2a1 1 0 0 1 1-.25 11.4 11.4 0 0 0 3.6.57 1 1 0 0 1 1 1V20a1 1 0 0 1-1 1A17 17 0 0 1 3 4a1 1 0 0 1 1-1h3.5a1 1 0 0 1 1 1c0 1.25.2 2.45.57 3.57a1 1 0 0 1-.25 1z"/></svg>
          0452817360
        </span>
        <span class="contact-item">
          <svg class="contact-icon" viewBox="0 0 24 24" aria-hidden="true"><rect x="2" y="5" width="20" height="14" rx="1" fill="#555555"/><path d="M3 6l9 7 9-7" fill="none" stroke="#f4f4f4" stroke-width="2"/></svg>
          GeraldFenwickPhotography47@mailbox.test
        </span>
      </div>
      <div class="contact-row">
        <span class="contact-item">
          <svg class="contact-icon contact-icon--line" viewBox="0 0 24 24" aria-hidden="true"><circle cx="12" cy="12" r="10"/><ellipse cx="12" cy="12" rx="4.5" ry="10"/><path d="M2 12h20"/></svg>
          www.GeraldFenwickPhotography.test.au
        </span>
        <span class="contact-item">
          <span class="social-square" aria-hidden="true"></span>
          Gerald_fenwick
        </span>
      </div>
    </div>
  </section>

  <section class="card card--back" aria-label="Business card, logo side">
    <div class="brand-mark"><span class="brand-name">Gerald<br>Fenwick</span></div>
    <p class="back-web">www.GeraldFenwickPhotography.test.au</p>
  </section>
</body>
</html>
```